RTavenor Business Cards & Letterhead

I have a logo but need a design for some new business cards. We are a Design-Build Firm that specializes in the design and construction of commercial projects.
the cards need to be professional. no cartoon stuff.
i would like to have the cards in AI format so I can update the card as needed. Logo is provided.
Our Address is: 4187 Marlowe Ct. Larkfield, Oregon 27614

```html
<!DOCTYPE html>
<html lang="en">
<head>
<meta charset="utf-8">
<title>RTavenor Business Card</title>
<link href="https://fonts.googleapis.com/css2?family=Open+Sans:wght@400;700&display=swap" rel="stylesheet">
<style>
  :root {
    --backdrop: #e6e4e1;
    --card-dark: #1f2025;
    --card-white: #ffffff;
    --brand-blue: #1f6db4;
    --brand-grey: #72747a;
    --text-light: #ecedf0;
    --rule: #c9cbd0;
  }
  * { box-sizing: border-box; margin: 0; padding: 0; }
  html, body {
    width: 1200px; height: 780px; overflow: hidden;
    background: var(--backdrop);
    font-family: "Open Sans", Arial, sans-serif;
  }
  .canvas { position: relative; width: 1200px; height: 780px; }

  .card {
    position: absolute; top: 241px;
    width: 520px; height: 297px;
    background: var(--card-dark);
    box-shadow: 0 10px 28px rgba(0,0,0,.22);
    overflow: hidden;
  }
  .card--front { left: 50px; }
  .card--back { left: 630px; }

  /* Front */
  .logo-band {
    position: absolute; left: 0; top: 0; bottom: 0; width: 94px;
    background: var(--card-white);
  }
  .logo-band .wordmark {
    position: absolute; left: 50%; top: 50%;
    transform: translate(-50%, -50%) rotate(-90deg);
    display: flex; align-items: center; gap: 8px;
    white-space: nowrap;
  }
  .wordmark-square { width: 16px; height: 16px; background: var(--brand-blue); }
  .wordmark-text {
    font-weight: 700; color: var(--brand-grey);
    letter-spacing: .5px; font-size: 27px; line-height: 1;
  }
  .name-rule {
    position: absolute; left: 94px; right: 0; top: 78px;
    height: 1px; background: var(--rule);
  }
  .name-tab {
    position: absolute; right: 0; top: 30px;
    width: 14px; height: 48px; background: var(--brand-blue);
  }
  .person {
    position: absolute; right: 26px; top: 26px; text-align: right;
  }
  .person-name {
    font-weight: 700; font-size: 22px; letter-spacing: .6px;
    color: var(--brand-blue); line-height: 1.1;
  }
  .person-title {
    font-size: 13px; color: var(--text-light); line-height: 1.4;
  }
  .contact {
    position: absolute; right: 26px; top: 160px;
    text-align: right; color: var(--text-light);
    font-size: 13px; line-height: 19px;
  }
  .address { margin-bottom: 10px; }
  .contact-row { display: flex; justify-content: flex-end; align-items: center; gap: 8px; }
  .contact-icon { width: 13px; height: 13px; flex: none; }

  /* Back */
  .card--back .wordmark {
    position: absolute; left: 50%; top: 50%;
    transform: translate(-50%, -50%);
    display: flex; align-items: center; gap: 12px;
  }
  .card--back .wordmark-square { width: 26px; height: 26px; }
  .card--back .wordmark-text { font-size: 50px; letter-spacing: 1px; }
</style>
</head>
<body>
<main class="canvas">

  <section class="card card--front" aria-label="Business card front">
    <div class="logo-band">
      <div class="wordmark">
        <span class="wordmark-square"></span>
        <span class="wordmark-text">RTAVENOR</span>
      </div>
    </div>
    <div class="name-rule"></div>
    <div class="name-tab"></div>
    <div class="person">
      <p class="person-name">RENATA TAVENOR</p>
      <p class="person-title">Founder/President</p>
    </div>
    <div class="contact">
      <p class="address">4187 Marlowe Ct. Larkfield,<br>Oregon 27614</p>
      <p class="contact-row">(555) 010-0148
        <svg class="contact-icon" viewBox="0 0 14 14" aria-hidden="true"><circle cx="7" cy="7" r="7" fill="var(--brand-blue)"/><path d="M4.3 3.6c.4-.3.8-.2 1 .2l.6 1.1c.2.3.1.6-.2.8l-.4.3c.4.9 1.1 1.6 2 2l.3-.4c.2-.3.5-.4.8-.2l1.1.6c.4.2.5.6.2 1l-.5.6c-.3.3-.8.4-1.2.2C6.4 9.2 4.8 7.6 4.2 6c-.2-.4-.1-.9.2-1.2z" fill="#fff"/></svg>
      </p>
      <p class="contact-row">www.rtavenor.com
        <svg class="contact-icon" viewBox="0 0 14 14" aria-hidden="true"><circle cx="7" cy="7" r="7" fill="var(--brand-blue)"/><circle cx="7" cy="7" r="4" fill="none" stroke="#fff" stroke-width="1"/><ellipse cx="7" cy="7" rx="1.7" ry="4" fill="none" stroke="#fff" stroke-width=".9"/><path d="M3 7h8" stroke="#fff" stroke-width=".9"/></svg>
      </p>
      <p class="contact-row">info@rtavenor.com
        <svg class="contact-icon" viewBox="0 0 14 14" aria-hidden="true"><circle cx="7" cy="7" r="7" fill="var(--brand-blue)"/><rect x="3.4" y="4.5" width="7.2" height="5" fill="none" stroke="#fff" stroke-width="1"/><path d="M3.4 4.6 7 7.4l3.6-2.8" fill="none" stroke="#fff" stroke-width="1"/></svg>
      </p>
    </div>
  </section>

  <section class="card card--back" aria-label="Business card back">
    <div class="wordmark">
      <span class="wordmark-square"></span>
      <span class="wordmark-text">RTAVENOR</span>
    </div>
  </section>

</main>
</body>
</html>
```